Wandering Rooms Stationary Set

Wandering Rooms is a bespoke interior design firm set to provide services to VIP clients with elegance and minimalism is the main theme for our stationary set. We require a full stationary set covering A4 letterhead, A4 & A3 envelopes, business cards, USB's, CDs, email signature and any other item the designer sees fit. logo is already designed and finalized, and we require the designer to use it as is without modifying the logo.

Address to be used on letterhead / business cards ...etc shall be as follows:

Phone : +971 2 518 2047
P.O. Box : 309186
Address: Block C&D, Bldg. 47, Court 12, Abu Dhabi, United Arab Emirates
Website: www.wanderingrooms-example.com

Target Market(s)

VIP Clients

Industry/Entity Type

Interior Design

Font styles to use
Other font styles liked:
• something to be unique

Colors

Designer to choose colors to be used in the design.

Requirements
Must have
• Elegant, minimalistic
Nice to have
• Simple yet elegant design having a sharp yet clean cut format
Should not have
• No additional colours, just colours that are used in the logo (silver, black or gold)

```html
<!DOCTYPE html>
<html lang="en">
<head>
<meta charset="utf-8">
<title>Wandering Rooms – Business Card</title>
<link rel="stylesheet" href="https://fonts.googleapis.com/css2?family=Arimo:wght@400;700&display=swap">
<style>
  :root {
    --backdrop: #a9a9a9;
    --card-dark: #6f6f6f;
    --card-light: #f1f1ef;
    --silver: #d2d2d2;
    --ink: #5b5b5b;
    --ink-strong: #505050;
  }
  * { margin: 0; padding: 0; box-sizing: border-box; }
  html, body {
    width: 1200px;
    height: 1017px;
    overflow: hidden;
    background: var(--backdrop);
    font-family: "Arimo", Arial, sans-serif;
  }
  .card {
    position: absolute;
    left: 340px;
    width: 548px;
    height: 310px;
  }
  .card--front { top: 158px; background: var(--card-dark); }
  .card--back  { top: 539px; background: var(--card-light); }

  .wordmark {
    position: absolute;
    font-weight: 400;
    letter-spacing: 0.18em;
    text-transform: uppercase;
    white-space: nowrap;
  }
  .card--front .wordmark {
    left: 0; right: 0; top: 140px;
    text-align: center;
    font-size: 22px;
    color: var(--silver);
  }
  .card--back .wordmark {
    left: 40px; top: 135px;
    font-size: 17px;
    color: #b4b4b4;
  }

  .contact {
    position: absolute;
    left: 326px;
    top: 84px;
    color: var(--ink);
    font-size: 12px;
    line-height: 16px;
  }
  .contact__name {
    font-size: 14px;
    font-weight: 700;
    color: var(--ink-strong);
    letter-spacing: 0.02em;
    line-height: 18px;
  }
  .contact__block { margin-top: 12px; }
</style>
</head>
<body>
  <section class="card card--front">
    <div class="wordmark">Wandering Rooms</div>
  </section>

  <section class="card card--back">
    <div class="wordmark">Wandering Rooms</div>
    <div class="contact">
      <div class="contact__name">SAMIR VALDANE</div>
      <div class="contact__role">General Manager</div>
      <div class="contact__block">
        Block C&amp;D, Bldg. 47, Court 12<br>
        Abu Dhabi, United Arab Emirates<br>
        P.O. Box: 309186
      </div>
      <div class="contact__block">
        Tel: +971 2 518 2047<br>
        www.wanderingrooms-example.com
      </div>
    </div>
  </section>
</body>
</html>
```